Business Card Design Project

We need a business card for a new technology services company. We develop software and implement software packages for our business customers and although we will begin with just one or two service offerings, our service offerings will expand over time. Our name comes from the an author, KL Barrow, and his "idea" was that opportunity should be based on ability and achievement, not on social status.

We would like to see a design that is standard in its size and shape, but stands apart in its dramatic color contrasts. The card should not use too many colors - the colors used in the background should highlight the brilliant blues of the logo (see attachment) to dramatic effect. The background should not be white.

If necessary, you can change the color of the words "KL Barrow", but not the word "Idea".

Card size should be U.S. standard 2 inches by 3.5 inches and provide for 1/8 inch bleed area on each side.

We need a design for both sides of the business card, one side communicating the company logo and contact information, the other side being purely graphical, incorporating the logo but no other information.

Contact Information Required:
Kate Brook
KateBrook@klbarrowvista.com
614-387-2259

Target Market(s)

Business executives

Industry/Entity Type

Software

Requirements
Must have
• It must have the full company logo on one side, and at least the graphic element of the logo on the other. Either that or the full logo on both.
Nice to have
• It would be nice to have a design that could work without needing two different textures. For example, it would be nice if the entire card could be shiny, not just parts of the card.

It would also be nice if texture is something we could add later.
Should not have
• The card should not use the color green.

```html
<!DOCTYPE html>
<html lang="en">
<head>
<meta charset="utf-8">
<title>Barrow Vista — Business Card</title>
<link rel="stylesheet" href="https://fonts.googleapis.com/css2?family=Questrial&family=Cinzel:wght@500&family=Arimo&display=swap">
<style>
  :root {
    --page: #e9ebee;
    --card-black: #0b0c0e;
    --card-sheen: #26282c;
    --brand-blue: #1c9ad8;
    --deep-blue: #0d6fa6;
    --steel-grey: #a9adb2;
    --text-white: #f4f6f8;
  }
  * { box-sizing: border-box; margin: 0; padding: 0; }
  html, body { width: 1200px; height: 750px; overflow: hidden; }
  body {
    background: var(--page);
    display: flex;
    align-items: center;
    justify-content: center;
    gap: 60px;
  }
  .card {
    position: relative;
    width: 520px;
    height: 297px;
    overflow: hidden;
    background: radial-gradient(ellipse at 45% 40%, var(--card-sheen) 0%, var(--card-black) 70%);
    box-shadow: 0 10px 28px rgba(0,0,0,0.28);
  }
  .card-art { position: absolute; inset: 0; width: 100%; height: 100%; }
  .company-name {
    position: absolute;
    font-family: "Questrial", sans-serif;
    font-weight: 400;
    color: var(--brand-blue);
    white-space: nowrap;
    display: flex;
    align-items: center;
    gap: 12px;
  }
  .brand-dot {
    display: inline-block;
    border-radius: 50%;
    background: var(--brand-blue);
  }
  .card-front .company-name { left: 40px; top: 78px; font-size: 36px; }
  .card-front .brand-dot { width: 16px; height: 16px; }
  .contact-list {
    position: absolute;
    left: 42px;
    top: 150px;
    list-style: none;
    font-family: "Arimo", sans-serif;
    font-size: 13px;
    color: var(--text-white);
  }
  .contact-list li { display: flex; align-items: center; gap: 8px; margin-bottom: 10px; }
  .contact-icon { width: 12px; height: 12px; flex: none; }
  .holder-name {
    position: absolute;
    right: 22px;
    top: 196px;
    font-family: "Cinzel", serif;
    font-weight: 500;
    font-size: 17px;
    color: var(--text-white);
    letter-spacing: 1px;
    white-space: nowrap;
  }
  .card-back .company-name {
    left: 50%;
    top: 50%;
    transform: translate(-50%, -50%);
    font-size: 48px;
  }
  .card-back .brand-dot { width: 24px; height: 24px; }
</style>
</head>
<body>

  <section class="card card-front" aria-label="Card front">
    <svg class="card-art" viewBox="0 0 520 297" aria-hidden="true">
      <polygon class="accent-band" points="0,262 520,150 520,206 130,297 0,297" fill="var(--brand-blue)"/>
      <polygon class="accent-stripe" points="160,297 520,216 520,224 196,297" fill="var(--steel-grey)"/>
    </svg>

    <h1 class="company-name"><span>Barrow Vista</span><span class="brand-dot"></span></h1>

    <ul class="contact-list">
      <li>
        <svg class="contact-icon" viewBox="0 0 12 12" aria-hidden="true"><path d="M3,1 L5,3.5 L3.8,5 C4.5,6.5 5.5,7.5 7,8.2 L8.5,7 L11,9 L9.5,11 C5,10.5 1.5,7 1,2.5 Z" fill="var(--brand-blue)"/></svg>
        <span>614-387-2259</span>
      </li>
      <li>
        <svg class="contact-icon" viewBox="0 0 12 12" aria-hidden="true"><rect x="0.5" y="2.5" width="11" height="7.5" rx="1" fill="var(--brand-blue)"/><path d="M1,3 L6,7 L11,3" fill="none" stroke="var(--card-black)" stroke-width="1"/></svg>
        <span>KateBrook@klbarrowvista.com</span>
      </li>
    </ul>

    <p class="holder-name">KATE BROOK</p>
  </section>

  <section class="card card-back" aria-label="Card back">
    <h2 class="company-name"><span class="brand-dot"></span><span>Barrow Vista</span></h2>
  </section>

</body>
</html>
```